Local Flower Farm Needs Business Card Design

I need business cards designed for a flower farm based in Eudora, Kansas.
Business Info:
We are a local cut flower farm located in Eudora, Kansas, founded by Corinne Haldwick. What started as a passion for agriculture and search for more joy in daily life has blossomed into a small business dedicated to providing the community with beautiful, fresh, and sustainable flowers. We specialize in local, seasonal blooms, ensuring that every petal reflects the care and dedication we pour into our craft. Our mission is to deliver the highest quality flowers directly to our customers through local farmers markets and to florists who share our commitment to sustainability. Join us in celebrating the beauty of nature, one bloom at a time!
Contact Details:
Corinne Haldwick
Owner
Phone 913-555-0147
Facebook: Rosalind Thorpe Gardens
Instagram: @RosalindThorpeGardens
Website: RosalindThorpeGardens.example
Target Market(s)
Wholesale to Florists and Direct to Consumer via Farmers Market
Industry/Entity Type
Florist, Farm
Contact Information for Business Card
Name, Contact Info, Logo
Look and feel
Each slider illustrates characteristics of the customer's brand and the style your logo design should communicate.

```html
<!DOCTYPE html>
<html lang="en">
<head>
<meta charset="utf-8">
<title>Rosalind Thorpe Gardens – Business Cards</title>
<link rel="stylesheet" href="https://fonts.googleapis.com/css2?family=Playfair+Display:wght@500;600&family=Lato:wght@400;700&display=swap">
<style>
  :root {
    --ink: #0b2a2d;
    --paper: #ffffff;
    --backdrop: #2b2b2b;
    --muted: #cfd9d9;
  }
  * { box-sizing: border-box; margin: 0; padding: 0; }
  html, body { width: 1200px; height: 875px; overflow: hidden; }
  body {
    background: var(--backdrop);
    display: flex;
    align-items: center;
    justify-content: center;
    gap: 40px;
    font-family: "Lato", sans-serif;
  }
  .card {
    position: relative;
    width: 540px;
    height: 310px;
    border-radius: 18px;
    overflow: hidden;
    box-shadow: 0 20px 40px rgba(0,0,0,.45);
  }
  .card__shape { position: absolute; inset: 0; width: 100%; height: 100%; }

  /* front */
  .card--front { background: var(--ink); }
  .front__name {
    position: absolute;
    left: 40px; top: 92px; width: 220px;
    text-align: center;
    font-family: "Playfair Display", serif;
    font-weight: 500;
    font-size: 22px;
    line-height: 1.25;
    letter-spacing: 2px;
    text-transform: uppercase;
    color: var(--ink);
  }
  .monogram-name {
    position: absolute;
    right: 22px; top: 44px; width: 130px;
    font-family: "Playfair Display", serif;
    font-weight: 600;
    font-size: 30px;
    line-height: 1.1;
    text-align: right;
  }
  .card--front .monogram-name { color: var(--paper); }
  .card__url {
    position: absolute;
    left: 0; right: 0; bottom: 24px;
    text-align: center;
    font-size: 15px;
    letter-spacing: 3.2px;
    text-transform: uppercase;
  }
  .card--front .card__url { color: var(--paper); }

  /* back */
  .card--back { background: var(--paper); }
  .card--back .monogram-name { color: var(--ink); top: 30px; }
  .card--back .card__url { color: var(--ink); }
  .contact {
    position: absolute;
    left: 34px; top: 84px;
    color: var(--paper);
  }
  .contact__name {
    font-family: "Playfair Display", serif;
    font-weight: 500;
    font-size: 21px;
    line-height: 1.1;
    letter-spacing: 1.5px;
    text-transform: uppercase;
  }
  .contact__role { font-size: 12px; margin: 4px 0 12px; color: var(--muted); }
  .contact__list { list-style: none; }
  .contact__item {
    display: flex; align-items: center; gap: 8px;
    font-size: 12px; line-height: 1.7;
  }
  .contact__icon { width: 10px; height: 10px; flex: none; }
  .dot { border-radius: 50%; border: 1.5px solid var(--paper); }
  .square { border: 1.5px solid var(--paper); border-radius: 2px; }
</style>
</head>
<body>

  <article class="card card--front">
    <svg class="card__shape" viewBox="0 0 540 310" aria-hidden="true">
      <polygon points="0,40 300,40 360,230 0,230" fill="var(--paper)"/>
    </svg>
    <p class="front__name">Rosalind Thorpe Gardens</p>
    <p class="monogram-name">Rosalind Thorpe Gardens</p>
    <p class="card__url">RosalindThorpeGardens.example</p>
  </article>

  <article class="card card--back">
    <svg class="card__shape" viewBox="0 0 540 310" aria-hidden="true">
      <polygon points="0,60 300,60 360,240 0,240" fill="var(--ink)"/>
    </svg>
    <div class="contact">
      <h1 class="contact__name">Corinne<br>Haldwick</h1>
      <p class="contact__role">Owner</p>
      <ul class="contact__list">
        <li class="contact__item">
          <svg class="contact__icon" viewBox="0 0 24 24" aria-hidden="true"><path fill="#fff" d="M6.6 10.8a15 15 0 0 0 6.6 6.6l2.2-2.2a1 1 0 0 1 1-.25 11.4 11.4 0 0 0 3.6.57 1 1 0 0 1 1 1V20a1 1 0 0 1-1 1A17 17 0 0 1 3 4a1 1 0 0 1 1-1h3.5a1 1 0 0 1 1 1c0 1.25.2 2.45.57 3.57a1 1 0 0 1-.25 1z"/></svg>
          913-555-0147
        </li>
        <li class="contact__item"><span class="contact__icon dot"></span>Rosalind Thorpe Gardens</li>
        <li class="contact__item"><span class="contact__icon square"></span>@RosalindThorpeGardens</li>
      </ul>
    </div>
    <p class="monogram-name">Rosalind Thorpe Gardens</p>
    <p class="card__url">RosalindThorpeGardens.example</p>
  </article>

</body>
</html>
```